Harrowmere Freight, Project

Company Profile
Harrowmere Freight Sdn Bhd is a well established and experienced freight forwarder in Kuala Lumpur, Malaysia. We specialize in air and sea forwarding, Custom Brokerage and regulatory compliance services, inland transportation,
overseas freighting and warehousing and distribution management. With our dedicated qualified and experienced professionals, we are fully committed to serving our clients.

Our Mission
Based on the motto “Quick, Reliable and Polite”, Harrowmere Freight is dedicated to upholding the following three points corporate philosophy:
1. Adhering to the principle that “the customer always comes first”.
2. Contributing to the development of the local community.
3. Making it our duty to be responsible and sincere.

Our Edge
• One-Stop Logistics Solutions
• Extensive Network Throughout Malaysia
• Highly Qualified and Experienced Pool of Professionals
• Comprehensive IT Solutions
• Innovative and Customer-focused Solutions
• Flexible and Consistent in Managing Exceptions
• Total Supply Chain Visibility

Target Market(s)

We sell the logistics services to all the industry in Malaysia. (ONE Stop Logistics Solutions)

Industry/Entity Type

Logistic

Contact Information for Business Card

I want the back of the card to be white with the logo and slogan. i would like to see the logo on the front with the general info.

Requirements
Must have
• Name, Title, Office, Cell, Fax, Email, Address, Website
Nice to have
• Modern Design Business Card

```html
<!DOCTYPE html>
<html lang="en">
<head>
<meta charset="utf-8">
<title>Harrowmere Freight — Stationery Set</title>
<link href="https://fonts.googleapis.com/css2?family=Montserrat:wght@500;700&family=Open+Sans:wght@400;600&display=swap" rel="stylesheet">
<style>
  :root{
    --bg:#e8e9eb;
    --paper:#ffffff;
    --paper-soft:#f3f3f4;
    --blue-dark:#1f64b0;
    --blue:#2a7fc6;
    --blue-light:#3a9bd8;
    --grey-dark:#4a4b4d;
    --grey:#6d6e70;
    --grey-light:#9a9b9d;
    --ink:#3a3b3d;
    --shadow:0 6px 18px rgba(0,0,0,.14);
  }
  *{box-sizing:border-box;margin:0;padding:0}
  html,body{width:1200px;height:874px;overflow:hidden}
  body{background:var(--bg);font-family:"Open Sans",Arial,sans-serif;color:var(--ink);position:relative}

  .piece{position:absolute;background:var(--paper);box-shadow:var(--shadow);overflow:hidden}

  .logo{display:flex;align-items:center;gap:6px;font-family:"Montserrat",Arial,sans-serif;font-weight:700;color:var(--blue-dark);line-height:1;white-space:nowrap}
  .logo__mark{width:10px;height:10px;background:var(--blue);flex:none}

  .faint-disc{position:absolute;border-radius:50%;background:var(--paper-soft)}

  /* Letterhead */
  .letterhead{left:40px;top:40px;width:300px;height:424px}
  .letterhead .logo{position:absolute;top:36px;left:0;right:0;justify-content:center;font-size:15px}
  .letterhead .faint-disc{width:190px;height:190px;left:55px;top:140px}
  .footer-band{position:absolute;left:0;right:0;bottom:0;height:22px;background:linear-gradient(90deg,var(--blue-dark),var(--blue-light));color:#fff;font-size:6.5px;display:flex;align-items:center;justify-content:space-between;padding:0 12px;white-space:nowrap}

  /* Folder */
  .folder{left:370px;top:40px;width:300px;height:424px}
  .folder .logo{position:absolute;top:40px;left:0;right:0;justify-content:center;font-size:16px}
  .folder__blue{position:absolute;left:0;right:0;top:120px;height:210px;background:linear-gradient(135deg,var(--blue-dark),var(--blue-light))}
  .folder__grey{position:absolute;left:0;right:0;bottom:0;height:94px;background:linear-gradient(90deg,var(--grey-dark),var(--grey-light));color:#e6e6e6;font-size:8px;display:flex;align-items:center;justify-content:center}

  /* Envelope */
  .envelope{left:700px;top:40px;width:460px;height:220px}
  .envelope__flap{position:absolute;left:0;right:0;top:0;height:46px;background:linear-gradient(90deg,var(--grey-dark),var(--grey));border-radius:0 0 10px 10px}
  .envelope .logo{position:absolute;left:22px;top:70px;font-size:14px}
  .envelope__web{position:absolute;left:0;right:0;bottom:20px;text-align:center;font-size:7.5px;color:var(--grey)}

  /* Compliment slip */
  .slip{left:700px;top:280px;width:460px;height:190px}
  .slip .faint-disc{width:150px;height:150px;right:40px;top:-30px}
  .slip .logo{position:absolute;left:30px;top:96px;font-size:15px}
  .slip .footer-band{height:20px;justify-content:flex-start}

  /* Business cards */
  .card{width:300px;height:172px}
  .card--front{left:40px;top:500px}
  .card--back{left:370px;top:500px}
  .card--front .logo{position:absolute;right:20px;top:20px;font-size:12px}
  .card__person{position:absolute;left:20px;top:64px}
  .card__name{font-family:"Montserrat",Arial,sans-serif;font-weight:700;font-size:11px;color:var(--blue-dark);letter-spacing:.5px}
  .card__title{font-size:7px;color:var(--grey)}
  .card__details{position:absolute;left:20px;top:96px;font-size:6.5px;line-height:1.55;color:var(--ink)}
  .card__address{position:absolute;right:20px;top:96px;font-size:6.5px;line-height:1.55;text-align:right;color:var(--ink)}
  .card__band{position:absolute;left:0;right:0;bottom:0;height:12px;background:linear-gradient(90deg,var(--blue-dark),var(--blue-light))}
  .card--back .logo{position:absolute;left:0;right:0;top:62px;justify-content:center;font-size:14px}
  .card__slogan{position:absolute;left:0;right:0;top:86px;text-align:center;font-size:8px;font-weight:600;letter-spacing:1px;color:var(--grey)}

  /* Notebook */
  .notebook{left:700px;top:500px;width:260px;height:340px}
  .notebook .logo{position:absolute;top:38px;left:24px;right:0;justify-content:center;font-size:14px}
  .notebook__blue{position:absolute;left:0;right:0;top:100px;height:160px;background:linear-gradient(135deg,var(--blue-dark),var(--blue-light))}
  .notebook__grey{position:absolute;left:0;right:0;bottom:0;height:80px;background:linear-gradient(90deg,var(--grey-dark),var(--grey-light));color:#e6e6e6;font-size:7px;display:flex;align-items:center;justify-content:flex-end;padding-right:18px}
  .notebook__spiral{position:absolute;left:6px;top:10px;width:8px;height:320px;z-index:2}

  /* Key tag */
  .keytag{left:990px;top:500px;width:160px;height:100px;border-radius:8px}
  .keytag .logo{position:absolute;inset:0;justify-content:center;font-size:11px}
</style>
</head>
<body>

<section class="piece letterhead" aria-label="Letterhead">
  <div class="faint-disc"></div>
  <div class="logo"><span class="logo__mark"></span>Harrowmere Freight</div>
  <div class="footer-band">
    <span>12 Jalan Ampang, 50450 Kuala Lumpur</span>
    <span>+60 3 2100 4400</span>
    <span>www.harrowmerefreight.com</span>
  </div>
</section>

<section class="piece folder" aria-label="Presentation folder">
  <div class="logo"><span class="logo__mark"></span>Harrowmere Freight</div>
  <div class="folder__blue"></div>
  <div class="folder__grey">www.harrowmerefreight.com</div>
</section>

<section class="piece envelope" aria-label="Envelope">
  <div class="envelope__flap"></div>
  <div class="logo"><span class="logo__mark"></span>Harrowmere Freight</div>
  <div class="envelope__web">www.harrowmerefreight.com</div>
</section>

<section class="piece slip" aria-label="Compliment slip">
  <div class="faint-disc"></div>
  <div class="logo"><span class="logo__mark"></span>Harrowmere Freight</div>
  <div class="footer-band"><span>12 Jalan Ampang, 50450 Kuala Lumpur, Malaysia</span></div>
</section>

<section class="piece card card--front" aria-label="Business card front">
  <div class="logo"><span class="logo__mark"></span>Harrowmere Freight</div>
  <div class="card__person">
    <div class="card__name">NADIA RAHMAN</div>
    <div class="card__title">General Manager</div>
  </div>
  <div class="card__details">
    Office +60 3 2100 4400<br>
    Cell +60 12 345 6789<br>
    Fax +60 3 2100 4401<br>
    nadia@harrowmerefreight.com
  </div>
  <div class="card__address">
    12 Jalan Ampang<br>
    50450 Kuala Lumpur<br>
    www.harrowmerefreight.com
  </div>
  <div class="card__band"></div>
</section>

<section class="piece card card--back" aria-label="Business card back">
  <div class="logo"><span class="logo__mark"></span>Harrowmere Freight</div>
  <div class="card__slogan">QUICK, RELIABLE AND POLITE</div>
  <div class="card__band"></div>
</section>

<section class="piece notebook" aria-label="Notebook">
  <div class="logo"><span class="logo__mark"></span>Harrowmere Freight</div>
  <div class="notebook__blue"></div>
  <div class="notebook__grey">www.harrowmerefreight.com</div>
  <svg class="notebook__spiral" viewBox="0 0 8 320" aria-hidden="true">
    <g fill="#3a3b3d">
      <circle cx="4" cy="10" r="3"/><circle cx="4" cy="30" r="3"/><circle cx="4" cy="50" r="3"/><circle cx="4" cy="70" r="3"/>
      <circle cx="4" cy="90" r="3"/><circle cx="4" cy="110" r="3"/><circle cx="4" cy="130" r="3"/><circle cx="4" cy="150" r="3"/>
      <circle cx="4" cy="170" r="3"/><circle cx="4" cy="190" r="3"/><circle cx="4" cy="210" r="3"/><circle cx="4" cy="230" r="3"/>
      <circle cx="4" cy="250" r="3"/><circle cx="4" cy="270" r="3"/><circle cx="4" cy="290" r="3"/><circle cx="4" cy="310" r="3"/>
    </g>
  </svg>
</section>

<section class="piece keytag" aria-label="Key tag">
  <div class="logo"><span class="logo__mark"></span>Harrowmere Freight</div>
</section>

</body>
</html>
```